Professional "Save the Date" Design

We are looking for a professional designer to create a clean, modern, and eye-catching "Save the Date" invitation that will be sent to a select group of physicians participating in our BRIGHTLANE Study.
Key Requirements:
The KORMAL logo should be clearly featured and lead the branding.
The OMBRA FLEX TQ logo should also appear but be subordinate to the KORMAL logo.
The design should be professional, modern, and easy to read — no busy or cluttered layouts.
The final product will be used in email communications (PDF or image format).
The project is time-sensitive: we would like to have the final version completed by end of day tomorrow.
Deliverables:
Final design in high-resolution PDF and image formats (PNG or JPG).
Editable file (Adobe Illustrator, InDesign, or similar) if possible.
Details:
Monday, June 23, 2025
4:30-5:15pm EST
Name of Call: BRIGHTLANE Investigator Call
Location: Virtual (PELTA Call)
Please include this blurb as well: "Join us for a BRIGHTLANE Study Investigator Call as we welcome all participating sites and provide key information to support a successful launch. We’ll cover points of contact, upcoming study-related events, and next steps as we begin site activation."
Physicians
Medical Device

```html
<!DOCTYPE html>
<html lang="en">
<head>
<meta charset="utf-8">
<title>Save the Date – BRIGHTLANE Investigator Call</title>
<link rel="stylesheet" href="https://fonts.googleapis.com/css2?family=Montserrat:wght@300;500;700;800&family=Questrial&display=swap">
<style>
  :root {
    --page-bg: #dedcdd;
    --brand-green: #6fb43f;
    --brand-navy: #0a2360;
    --white: #ffffff;
    --font-display: "Montserrat", "Century Gothic", sans-serif;
    --font-body: "Questrial", "Century Gothic", sans-serif;
  }
  * { margin: 0; padding: 0; box-sizing: border-box; }
  html, body {
    width: 1200px;
    height: 1200px;
    overflow: hidden;
    background: var(--page-bg);
  }
  .flyer {
    position: absolute;
    left: 231px;
    top: 83px;
    width: 738px;
    height: 1033px;
    background: var(--brand-green);
    overflow: hidden;
  }
  .flyer__art {
    position: absolute;
    inset: 0;
    width: 738px;
    height: 1033px;
  }
  .wave { fill: var(--brand-navy); }
  .brand-primary {
    font-family: var(--font-body);
    fill: var(--brand-green);
  }
  .brand-secondary {
    font-family: var(--font-display);
    font-weight: 700;
    fill: var(--white);
  }
  .headline {
    font-family: var(--font-display);
    fill: var(--white);
  }
  .headline--save { font-weight: 500; }
  .headline--the { font-weight: 300; }
  .headline--date { font-weight: 800; }
  .call-band { fill: var(--brand-navy); }
  .call-title {
    font-family: var(--font-display);
    font-weight: 700;
    fill: var(--white);
  }
  .event-details {
    position: absolute;
    left: 21px;
    top: 706px;
    font-family: var(--font-display);
    font-weight: 700;
    font-size: 29px;
    line-height: 47px;
    color: var(--white);
    list-style: none;
  }
  .event-blurb {
    position: absolute;
    left: 23px;
    top: 888px;
    font-family: var(--font-body);
    font-size: 21px;
    line-height: 31px;
    color: var(--white);
  }
  .event-blurb__line {
    display: block;
    white-space: nowrap;
  }
</style>
</head>
<body>
  <main class="flyer">
    <svg class="flyer__art" viewBox="0 0 738 1033">
      <path class="wave" d="M344 0 L738 0 L738 663 C720 500 592 400 498 325 C398 244 344 150 344 25 Z"/>

      <text class="brand-primary" x="710" y="138" font-size="140" text-anchor="end" textLength="289" lengthAdjust="spacingAndGlyphs">KORMAL</text>
      <text class="brand-secondary" x="714" y="226" font-size="32" text-anchor="end" textLength="124" lengthAdjust="spacingAndGlyphs">OMBRA FLEX TQ</text>

      <text class="headline headline--save" x="25" y="435" font-size="174" textLength="388" lengthAdjust="spacingAndGlyphs">SAVE</text>
      <text class="headline headline--the" transform="translate(474 433) rotate(-90)" font-size="68" textLength="118" lengthAdjust="spacingAndGlyphs">THE</text>
      <text class="headline headline--date" x="28" y="585" font-size="200" textLength="446" lengthAdjust="spacingAndGlyphs">DATE</text>

      <path class="call-band" d="M0 618 L563 618 A31 31 0 0 1 563 680 L0 680 Z"/>
      <text class="call-title" x="25" y="663" font-size="40" textLength="543" lengthAdjust="spacingAndGlyphs">BRIGHTLANE Investigator Call</text>
    </svg>

    <ul class="event-details">
      <li class="event-details__date">Monday, June 23, 2025</li>
      <li class="event-details__time">4:30-5:15pm EST</li>
      <li class="event-details__location">Location: Virtual (PELTA Call)</li>
    </ul>

    <p class="event-blurb">
      <span class="event-blurb__line">Join us for a BRIGHTLANE Study Investigator Call as we welcome all</span>
      <span class="event-blurb__line">participating sites and provide key information to support a successful</span>
      <span class="event-blurb__line">launch. We’ll cover points of contact, upcoming study-related events,</span>
      <span class="event-blurb__line">and next steps as we begin site activation.</span>
    </p>
  </main>
</body>
</html>
```